Card Design for my dog training business Brightpaw Obedience

Need a business card design for my dog training business with my new logo. Want the card to come off professional yet fun. Want it to be very eye catchy as well. I normally have these at vet clinics, pet stores, and groomers. so need it to look better than my competitors.
Target Market(s)
dog owners
Industry/Entity Type
Dog Training
Contact Information for Business Card
needs logo, my name and info
Font styles to use
Serif
Colors
0255a3
ffffff
ec1f27
000000
333333
fbfbfb
Requirements
Must have
- Brightpaw Obedience
- Felix Orland
- 415 903 2276
- info@brightpawobedience.example
- www.brightpawobedience.example

```html
<!DOCTYPE html>
<html lang="en">
<head>
<meta charset="utf-8">
<title>Brightpaw Obedience – Business Card</title>
<link href="https://fonts.googleapis.com/css2?family=Cormorant+Garamond:ital,wght@0,500;1,500&family=Lato:wght@400&display=swap" rel="stylesheet">
<style>
  :root {
    --backdrop: #333333;
    --card: #ffffff;
    --card-soft: #fbfbfb;
    --ink: #000000;
    --ink-soft: #333333;
    --pattern: #ececec;
  }
  * { box-sizing: border-box; margin: 0; padding: 0; }
  html, body { width: 1200px; height: 1108px; overflow: hidden; background: var(--backdrop); }
  .sheet {
    position: relative; width: 1200px; height: 1108px;
    display: flex; justify-content: center; align-items: center; gap: 80px;
  }
  .card {
    position: relative; width: 460px; height: 800px;
    background: var(--card); border-radius: 26px; overflow: hidden;
    color: var(--ink);
  }
  .card--front { display: flex; flex-direction: column; align-items: center; padding-top: 150px; }
  .brand-mark {
    display: flex; align-items: center; gap: 14px;
    font-family: "Cormorant Garamond", serif; font-weight: 500;
    font-size: 38px; line-height: 1.1; color: var(--ink); text-align: center;
    white-space: nowrap;
  }
  .brand-mark__square { width: 18px; height: 18px; background: var(--ink); flex: none; }
  .brand-rule { width: 250px; border-top: 2px solid var(--ink); margin-top: 16px; }
  .tagline {
    margin-top: 14px; font-family: "Cormorant Garamond", serif; font-style: italic;
    font-size: 15px; color: var(--ink-soft); white-space: nowrap;
  }
  .holder {
    margin-top: 74px; font-family: "Cormorant Garamond", serif; font-weight: 500;
    font-size: 34px; letter-spacing: 1px; text-transform: uppercase;
  }
  .contact-divider { display: flex; align-items: center; gap: 10px; margin-top: 20px; }
  .contact-divider__line { width: 110px; border-top: 1.5px solid var(--ink); }
  .contact-icon { width: 26px; height: 26px; display: block; }
  .contact-list {
    margin-top: 18px; text-align: center; font-family: "Lato", sans-serif;
    font-size: 23px; line-height: 1.4; font-style: normal; white-space: nowrap;
  }
  .card--back { display: flex; flex-direction: column; align-items: center; }
  .pattern-field {
    position: absolute; inset: 0;
    background: linear-gradient(180deg, var(--pattern) 0%, var(--card-soft) 70%, var(--card) 100%);
  }
  .back-mark { position: absolute; left: 0; right: 0; bottom: 120px; display: flex; flex-direction: column; align-items: center; }
</style>
</head>
<body>
<main class="sheet">
  <section class="card card--front">
    <div class="brand-mark"><span class="brand-mark__square"></span>Brightpaw Obedience</div>
    <div class="brand-rule"></div>
    <p class="tagline">“Teaching good manners to dogs one at a time.”</p>
    <h1 class="holder">Felix Orland</h1>
    <div class="contact-divider">
      <span class="contact-divider__line"></span>
      <svg class="contact-icon" viewBox="0 0 26 26" aria-label="phone">
        <rect width="26" height="26" fill="#000"/>
        <path d="M8 7h3l1 4-2 1a8 8 0 0 0 4 4l1-2 4 1v3c-7 0-11-4-11-11z" fill="#fff"/>
      </svg>
      <svg class="contact-icon" viewBox="0 0 26 26" aria-label="email">
        <rect width="26" height="26" fill="#000"/>
        <rect x="6" y="8" width="14" height="10" fill="none" stroke="#fff" stroke-width="1.6"/>
        <path d="M6 8l7 6 7-6" fill="none" stroke="#fff" stroke-width="1.6"/>
      </svg>
      <svg class="contact-icon" viewBox="0 0 26 26" aria-label="website">
        <rect width="26" height="26" fill="#000"/>
        <circle cx="13" cy="13" r="6.5" fill="none" stroke="#fff" stroke-width="1.6"/>
        <path d="M6.5 13h13M13 6.5c-3 3.5-3 9.5 0 13M13 6.5c3 3.5 3 9.5 0 13" fill="none" stroke="#fff" stroke-width="1.2"/>
      </svg>
      <span class="contact-divider__line"></span>
    </div>
    <address class="contact-list">
      <div>415 903 2276</div>
      <div>info@brightpawobedience.example</div>
      <div>www.brightpawobedience.example</div>
    </address>
  </section>

  <section class="card card--back">
    <div class="pattern-field" role="img" aria-label="Faint soft grey wash across the card back"></div>
    <div class="back-mark">
      <div class="brand-mark"><span class="brand-mark__square"></span>Brightpaw Obedience</div>
      <div class="brand-rule"></div>
    </div>
  </section>
</main>
</body>
</html>
```